Ridgeline Haul Carriers - Website

A clean, not cluttered informative website for our business. We specialize in the transportation of radioactive materials across North America. The site is mostly for information about our company and will not be used to attract business but will be used to attract employee's mainly drivers. Driver's are very hard to find in our area. One of the pages needs to be a job's posting page with an apply now button. Either an application can be filled out there or a resume can be uploaded which ever functionality works better. I would like a website that I can easily edit, ability to change text and photos.

Number of Pages Required

5+ page

Colors

Designer to choose colors to be used in the design.

Requirements
Must have
• Home - About - Services - Jobs - Contact pages
• A way prospective employee's can apply or upload their resume to be emailed to me
• Very clean apperance
Should not have
• I don't want it to be busy

```html
<!DOCTYPE html>
<html lang="en">
<head>
<meta charset="utf-8">
<title>Ridgeline Haul Carriers</title>
<link href="https://fonts.googleapis.com/css2?family=Roboto:wght@400;500;700&display=swap" rel="stylesheet">
<style>
:root{
  --brand:#1a5aad;
  --brand-dark:#144a90;
  --ink:#333;
  --text:#5a5a5a;
  --muted:#777;
  --card-light:#e4f0fc;
  --white:#fff;
  --footer:#000;
}
*{margin:0;padding:0;box-sizing:border-box}
html,body{width:1200px;height:3390px;overflow:hidden}
body{position:relative;background:var(--white);font-family:'Roboto',sans-serif;color:var(--ink)}
.abs{position:absolute}

.top-bar{left:0;top:0;width:1200px;height:7px;background:var(--brand)}
.site-header{left:0;top:7px;width:1200px;height:85px;background:var(--white)}
.brand-name{left:68px;top:22px;font-size:27px;font-weight:700;color:var(--brand);letter-spacing:.5px;line-height:1}
.brand-sub{left:68px;top:54px;font-size:11px;font-weight:500;color:var(--brand);letter-spacing:6px}
.main-nav{right:242px;top:34px;display:flex;gap:36px;font-size:16px;color:var(--ink);white-space:nowrap}
.social-top{right:86px;top:37px;display:flex;gap:36px}
.dot{width:14px;height:14px;border-radius:50%;background:var(--ink)}

.hero{left:0;top:92px;width:1200px;height:523px;background:linear-gradient(180deg,#8d8a86 0%,#6e6660 40%,#53504e 70%,#3d3b3a 100%)}
.hero-arrow{top:380px}

.section-title{left:0;width:1200px;display:flex;justify-content:center;align-items:center;gap:18px;font-size:29px;font-weight:700;color:var(--brand)}
.section-title .bars{width:50px;height:12px;border-top:3px solid var(--muted);border-bottom:3px solid var(--muted)}

.about-photo{left:314px;top:782px;width:811px;height:560px;background:radial-gradient(circle at 50% 45%,#f3c36a 0%,#c46b1e 25%,#4a2a14 60%,#120b07 100%)}
.about-card{left:75px;top:834px;width:508px;height:447px;background:var(--white);border-left:4px solid var(--brand);padding:40px 38px 0 36px;box-shadow:0 4px 18px rgba(0,0,0,.08)}
.about-card h2{font-size:29px;font-weight:500;color:#555;line-height:1.2}
.rule{width:54px;height:2px;background:#bbb;margin:22px 0 18px}
.lead{font-size:17px;font-weight:500;color:#555;line-height:1.5}
.body-text{font-size:13px;color:var(--text);line-height:2;margin-top:6px}
.btn{display:inline-block;background:var(--brand);color:var(--white);font-size:16px;font-weight:500;padding:10px 20px;margin-top:24px}

.services-photo{left:75px;top:1503px;width:811px;height:520px;background:linear-gradient(180deg,#ffffff 0%,#f5cf27 22%,#e8b50e 60%,#d9d5cc 90%,#ffffff 100%)}
.services-card{left:615px;top:1593px;width:472px;padding:40px 14px 26px 40px;background:var(--white);box-shadow:0 4px 18px rgba(0,0,0,.1)}
.services-card .lead{font-size:17px;font-weight:400;color:#555}
.services-card .body-text{margin-top:18px}
.services-card .btn{margin-top:14px}

.job-card{top:2210px;width:515px;height:298px;padding:28px 36px 0 36px}
.job-card h3{font-size:27px;font-weight:700}
.job-card p{font-size:13px;line-height:2.1;margin-top:12px}
.job-owner{left:75px;background:var(--brand);color:var(--white)}
.job-owner .btn{background:transparent;border:2px solid var(--white);margin-top:22px}
.job-company{left:610px;background:var(--card-light);color:var(--brand)}
.job-company .btn{margin-top:22px}

.map{left:0;top:2599px;width:1200px;height:520px;background:linear-gradient(135deg,#cfe3f6 0%,#e6efd9 30%,#eef1e6 60%,#d9e7c8 100%)}

.contact-row{left:0;top:3150px;width:1200px;display:flex;justify-content:center;gap:34px;font-size:15px;color:#444}
.contact-row span{display:flex;align-items:center;gap:10px}

.site-footer{left:0;top:3211px;width:1200px;height:179px;background:var(--footer);color:var(--white)}
.footer-nav{left:0;top:40px;width:1200px;display:flex;justify-content:center;gap:28px;font-size:15px}
.footer-nav .active{font-weight:700}
.footer-social{left:0;top:91px;width:1200px;display:flex;justify-content:center;gap:38px}
.footer-social .dot{background:var(--white)}
.copyright{left:0;top:134px;width:1200px;text-align:center;font-size:13px}
.page-mark{right:40px;top:134px;font-size:12px}
</style>
</head>
<body>
<div class="abs top-bar"></div>
<header class="abs site-header">
  <div class="abs brand-name">RIDGELINE HAUL</div>
  <div class="abs brand-sub">CARRIERS</div>
  <nav class="abs main-nav"><span>Home</span><span>About Us</span><span>Services</span><span>Jobs</span><span>Contact Us</span></nav>
  <div class="abs social-top"><span class="dot"></span><span class="dot"></span><span class="dot"></span></div>
</header>

<section class="abs hero" role="img" aria-label="Photo of a tractor-trailer hauling secured cylindrical containers">
  <svg class="abs hero-arrow" style="left:72px" width="18" height="24" viewBox="0 0 18 24"><path d="M14 2 4 12l10 10" fill="none" stroke="#fff" stroke-width="4"/></svg>
  <svg class="abs hero-arrow" style="left:1110px" width="18" height="24" viewBox="0 0 18 24"><path d="M4 2l10 10L4 22" fill="none" stroke="#fff" stroke-width="4"/></svg>
</section>

<div class="abs section-title" style="top:686px"><span class="bars"></span>ABOUT US<span class="bars"></span></div>
<div class="abs about-photo" role="img" aria-label="Glowing radiation hazard symbol with sparks"></div>
<article class="abs about-card">
  <h2>WELCOME TO<br>RIDGELINE HAUL CARRIERS</h2>
  <div class="rule"></div>
  <p class="lead">We specialize in the transportation of radioactive materials across North America .</p>
  <p class="body-text">Lorem ipsum dolor sit amet, consectetur adipiscing elit, sed do eiusmod tempor incididunt ut labore et dolore magna aliqua. Ut enim ad minim veniam, quis nostrud exercitation ullamco laboris nisi ut aliquip ex ea commodo consequat. Duis aute irure dolor in reprehenderit in voluptate velit esse cillum dolore eu fugiat nulla pariatur.</p>
  <span class="btn">READ MORE</span>
</article>

<div class="abs section-title" style="top:1409px"><span class="bars"></span>SERVICES<span class="bars"></span></div>
<div class="abs services-photo" role="img" aria-label="Yellow radioactive waste barrels"></div>
<article class="abs services-card">
  <p class="lead">Lorem ipsum dolor sit amet, consectetur adipiscing elit, sed do eiusmod tempor incididunt ut</p>
  <p class="body-text">abore et dolore magna aliqua. Ut enim ad minim veniam, quis nostrud exercitation ullamco laboris nisi ut aliquip ex ea commodo consequat. Duis aute irure dolor in reprehenderit in voluptate velit esse cillum dolore eu fugiat nulla pariatur.</p>
  <span class="btn">READ MORE</span>
</article>

<div class="abs section-title" style="top:2105px"><span class="bars"></span>JOB'S POSTING<span class="bars"></span></div>
<article class="abs job-card job-owner">
  <h3>OWNER/OPERATORS</h3>
  <p>Lorem ipsum dolor sit amet, consectetur adipiscing elit, sed do eiusmod tempor incididunt ut abore et dolore magna aliqua. Ut enim ad minim veniam, quis nostrud exercitation ullamco laboris nisi ut aliquip ex ea commodo consequat. ...</p>
  <span class="btn">APPLY NOW</span>
</article>
<article class="abs job-card job-company">
  <h3>COMPANY DRIVERS</h3>
  <p>Lorem ipsum dolor sit amet, consectetur adipiscing elit, sed do eiusmod tempor incididunt ut abore et dolore magna aliqua. Ut enim ad minim veniam, quis nostrud exercitation ullamco laboris nisi ut aliquip ex ea commodo consequat. ...</p>
  <span class="btn">APPLY NOW</span>
</article>

<div class="abs map" role="img" aria-label="Road map showing driving routes from the company yard to New York"></div>

<div class="abs contact-row">
  <span><svg width="12" height="16" viewBox="0 0 12 16"><path d="M6 0a6 6 0 0 0-6 6c0 4.5 6 10 6 10s6-5.5 6-10a6 6 0 0 0-6-6zm0 8.5A2.5 2.5 0 1 1 6 3.5a2.5 2.5 0 0 1 0 5z" fill="#333"/></svg>412 Cedar Bend Road, Harlow Falls, NY 13420</span>
  <span><svg width="15" height="15" viewBox="0 0 16 16"><path d="M3.6 1 6 3.8 4.6 5.6c.9 2 2.5 3.6 4.6 4.6l1.7-1.5L14.9 11 13.6 14C7 14.6 1.4 9 2 2.4z" fill="#333"/></svg>1-800-555-0148</span>
  <span><svg width="16" height="12" viewBox="0 0 16 12"><path d="M0 0h16v12H0z" fill="#333"/><path d="M0 0l8 6 8-6" fill="none" stroke="#fff" stroke-width="1.4"/></svg>hello@ridgelinehaul.example</span>
</div>

<footer class="abs site-footer">
  <nav class="abs footer-nav"><span class="active">Home</span><span>About Us</span><span>Services</span><span>Jobs</span><span>Contact Us</span></nav>
  <div class="abs footer-social"><span class="dot"></span><span class="dot"></span><span class="dot"></span><span class="dot"></span><span class="dot"></span></div>
  <div class="abs copyright">© 2019 | www.ridgelinehaul.example</div>
  <div class="abs page-mark">M1</div>
</footer>
</body>
</html>
```